Business Card for my New Brokerage

Looking to get a business card design for my new Real Estate Brokerage.
I want it with Picture, Phone Number, Email, Website, Office Address
Name and Designation. Please add logo too.

Target Market(s)

Real Estate Investors or Home Buyers

Industry/Entity Type

Real Estate

Contact Information for Business Card

Name, Email, Phone Number, website, email, office address

Colors
EB3D1F
EC4F4E
F09395
F8D3D4
FCEDEE

Requirements
Must have
• Minimalistic, Clean, Modern, Photo
Nice to have
• White and Red Colors

```html
<!DOCTYPE html>
<html lang="en">
<head>
<meta charset="UTF-8">
<title>Ember Realty Inc — Business Card</title>
<link rel="stylesheet" href="https://fonts.googleapis.com/css2?family=Montserrat:wght@400;500;700&display=swap">
<style>
  :root {
    --red: #dd0000;
    --red-deep: #c40000;
    --white: #ffffff;
    --gold: #d9b45a;
    --backdrop: #b1b2ad;
    --photo-a: #e9e4df;
    --photo-b: #3a3f4a;
  }
  * { margin: 0; padding: 0; box-sizing: border-box; }
  html, body {
    width: 1200px; height: 801px; overflow: hidden;
    background: var(--backdrop);
    font-family: "Montserrat", sans-serif;
  }
  .stage {
    position: relative; width: 1200px; height: 801px;
    display: flex; flex-direction: column; align-items: center; justify-content: center; gap: 60px;
  }
  .card {
    position: relative; width: 560px; height: 320px; overflow: hidden;
    box-shadow: 0 10px 24px rgba(0,0,0,0.25);
  }
  .card-front { background: var(--white); }
  .card-front .shapes { position: absolute; inset: 0; }
  .brand {
    position: absolute; left: 42px; top: 92px; color: var(--red);
    display: flex; flex-direction: column; align-items: flex-start;
  }
  .brand-name {
    font-weight: 700; font-size: 50px; letter-spacing: 1px; line-height: 1;
    display: flex; align-items: flex-start; gap: 6px;
  }
  .brand-dot { width: 8px; height: 8px; background: currentColor; margin-top: 4px; }
  .brand-sub {
    font-weight: 500; font-size: 14px; letter-spacing: 6px; margin-top: 6px; margin-left: 40px;
  }
  .address {
    position: absolute; left: 28px; bottom: 18px; color: var(--white);
    font-size: 12px; line-height: 1.45; font-weight: 400;
  }
  .contact {
    position: absolute; left: 352px; top: 160px; color: var(--white);
  }
  .contact-name { font-weight: 700; font-size: 19px; letter-spacing: 1px; }
  .contact-title { font-size: 12px; margin-top: 2px; margin-bottom: 10px; }
  .contact-line {
    font-size: 12px; line-height: 1.6; display: flex; align-items: center; gap: 5px;
  }
  .contact-line svg { width: 10px; height: 10px; flex: none; }
  .card-back {
    background: var(--red); color: var(--white);
    display: flex; align-items: center; justify-content: center;
  }
  .card-back .brand { position: static; color: var(--white); }
  .card-back .brand-name { font-size: 76px; gap: 8px; }
  .card-back .brand-dot { width: 11px; height: 11px; margin-top: 6px; }
  .card-back .brand-sub { font-size: 20px; letter-spacing: 9px; margin-left: 62px; margin-top: 8px; }
</style>
</head>
<body>
<main class="stage">
  <section class="card card-front">
    <svg class="shapes" viewBox="0 0 560 320" width="560" height="320">
      <defs>
        <radialGradient id="photoTone" cx="50%" cy="45%" r="60%">
          <stop offset="0%" stop-color="var(--photo-a)"/>
          <stop offset="100%" stop-color="var(--photo-b)"/>
        </radialGradient>
      </defs>
      <path class="swoosh-gold" d="M0 242 C120 240 230 222 284 170 C334 118 366 28 462 0 L472 0 C376 32 346 124 296 176 C240 232 128 254 0 256 Z" fill="var(--gold)"/>
      <path class="swoosh-red" d="M480 0 L560 0 L560 320 L0 320 L0 262 C130 262 246 238 300 182 C350 128 384 36 480 0 Z" fill="var(--red)"/>
      <circle class="photo-frame" cx="408" cy="80" r="64" fill="var(--white)" stroke="var(--red-deep)" stroke-width="2"/>
      <circle class="photo" cx="408" cy="80" r="58" fill="url(#photoTone)" role="img" aria-label="Portrait photo of the agent"/>
    </svg>

    <div class="brand">
      <div class="brand-name">EMBER<span class="brand-dot"></span></div>
      <div class="brand-sub">REALTY INC</div>
    </div>

    <div class="address">
      1870 Willow Creek Drive<br>
      Maple Hollow, GA 30412
    </div>

    <div class="contact">
      <div class="contact-name">DANIEL HARPER</div>
      <div class="contact-title">Founder and President</div>
      <div class="contact-line">+330 5184-2270
        <svg viewBox="0 0 10 10"><path d="M2 1 L4 1 L4.6 3 L3.4 3.8 C4 5 5 6 6.2 6.6 L7 5.4 L9 6 L9 8 C5 8.5 1.5 5 2 1 Z" fill="var(--white)"/></svg>
      </div>
      <div class="contact-line">info@emberrealtyinc.com
        <svg viewBox="0 0 10 10"><rect x="1" y="2" width="8" height="6" fill="none" stroke="var(--white)"/><path d="M1 2 L5 5.5 L9 2" fill="none" stroke="var(--white)"/></svg>
      </div>
      <div class="contact-line">www.emberrealtyinc.com
        <svg viewBox="0 0 10 10"><circle cx="5" cy="5" r="4" fill="none" stroke="var(--white)"/><path d="M1 5 H9 M5 1 C3 3 3 7 5 9 M5 1 C7 3 7 7 5 9" fill="none" stroke="var(--white)" stroke-width="0.8"/></svg>
      </div>
    </div>
  </section>

  <section class="card card-back">
    <div class="brand">
      <div class="brand-name">EMBER<span class="brand-dot"></span></div>
      <div class="brand-sub">REALTY INC</div>
    </div>
  </section>
</main>
</body>
</html>
```